Brisk Harbor claims recovery services

Its a new company in Dubai UAE. The company activity is debt management, debt collection, loans settlements and restructuring. The company involved in any business or sector requires debt management including government entities, Medical & Health care sector, Banks & finance companies, SME's and commercial business.

Target Market(s)

government entities, Medical & Health care sector, Banks & finance companies, SME's and commercial business.

Industry/Entity Type

Financial Service

Number of Pages Required

5+ page

Requirements
Must have
• Focus on the services not the team and clients
Should not have
• Colorful . Shouldn't have Client testimonial and our clients

```html
<!DOCTYPE html>
<html lang="en">
<head>
<meta charset="utf-8">
<title>Brisk Harbor — Claims Recovery Services</title>
<link href="https://fonts.googleapis.com/css2?family=Cinzel:wght@400;700&family=Open+Sans:wght@400;600;700;800&family=Roboto+Condensed:wght@400&display=swap" rel="stylesheet">
<style>
:root{
  --navy:#2b5d85;
  --navy-deep:#244f73;
  --topbar:#2c6690;
  --ink:#5c5c5c;
  --grey-head:#8b8b8b;
  --circle:#ececec;
  --field-line:#c9c9c9;
  --white:#ffffff;
  --serif:"Cinzel", "Times New Roman", serif;
  --sans:"Open Sans", Arial, sans-serif;
  --cond:"Roboto Condensed", "Arial Narrow", sans-serif;
}
*{box-sizing:border-box;margin:0;padding:0}
html,body{width:1200px;height:2439px;overflow:hidden;background:var(--white)}
body{position:relative;font-family:var(--sans);color:var(--ink)}
.abs{position:absolute}

/* top bar */
.topbar{left:0;top:0;width:1200px;height:42px;background:var(--topbar);color:var(--white)}
.topbar .mail{left:716px;top:10px;font-size:16px;display:flex;align-items:center;gap:8px}
.topbar .phone{left:964px;top:7px;font-size:21px;font-weight:700;display:flex;align-items:center;gap:8px}

/* header */
.brand{left:70px;top:110px;width:240px;text-align:center;font-family:var(--serif);color:var(--navy)}
.brand .name{font-size:27px;line-height:34px;letter-spacing:.5px;white-space:nowrap;display:flex;align-items:center;justify-content:center;gap:8px}
.brand .mark{flex:none;width:11px;height:11px;background:var(--navy)}
.brand .tag{font-size:8px;line-height:12px;letter-spacing:2px;color:var(--grey-head);border-top:1px solid #bbb;margin:3px 12px 0;padding-top:3px;white-space:nowrap}
.nav{top:100px;font-family:var(--serif);font-size:18px;color:var(--grey-head);letter-spacing:1px}
.nav.active{color:var(--navy);font-weight:700}

/* hero */
.hero{left:0;top:168px;width:1200px;height:574px;background:linear-gradient(110deg,#d9dde2 0%,#e9ecef 35%,#b8c2cc 60%,#3a4656 85%,#2a3340 100%)}
.hero h1{position:absolute;left:0;width:1200px;top:200px;text-align:center;color:var(--white);font-size:42px;font-weight:700;line-height:62px;letter-spacing:-0.5px;text-shadow:0 2px 6px rgba(0,0,0,.35)}

/* welcome */
.welcome-mark{left:582px;top:818px;width:36px;height:36px;border-radius:50%;background:var(--navy)}
.section-title{font-family:var(--serif);font-size:46px;font-weight:400;color:var(--grey-head);letter-spacing:1px;white-space:nowrap}
.section-title b{color:var(--navy);font-weight:400}
.welcome-title{left:0;width:1200px;top:868px;text-align:center}
.welcome-text{left:130px;width:940px;top:942px;text-align:center;font-size:15.5px;line-height:25.5px}
.sector{width:240px;text-align:center}
.sector .ring{width:114px;height:114px;margin:0 auto;border-radius:50%;background:var(--circle);display:flex;align-items:center;justify-content:center}
.sector .label{margin-top:18px;font-family:var(--serif);font-size:19px;line-height:31px;color:#333;letter-spacing:.5px}

/* services */
.services{left:0;top:1302px;width:1200px;height:324px;background:linear-gradient(90deg,#dcdcdc 0%,#efefef 45%,#e4e4e4 100%)}
.services-title{left:0;width:1200px;top:1347px;text-align:center;font-size:48px}
.service-img{width:208px;height:140px}
.service-title{font-family:var(--cond);font-size:24px;font-weight:400;color:var(--navy)}
.service-text{font-size:15.5px;line-height:26px;color:#666;width:300px}
.read-more{font-size:15px;font-weight:700;color:var(--navy);display:flex;align-items:center;gap:4px}

/* news */
.news-title{left:81px;top:1672px;font-size:42px}
.news-date{left:78px;width:76px;height:62px;border:1px solid #d6d6d6;border-radius:3px;overflow:hidden;text-align:center}
.news-date .day{height:40px;background:#a3a3a3;color:var(--white);font-size:28px;font-weight:700;line-height:40px}
.news-date .mon{font-size:14px;line-height:22px;color:#666}
.news-item{left:167px;width:400px}
.news-item h3{font-size:18px;font-weight:400;color:var(--navy);line-height:24px}
.news-item p{font-size:15.5px;line-height:25px;color:#666}
.news-item p span{color:var(--navy)}

/* contact form */
.touch-title{left:647px;top:1672px;font-size:42px}
.field{border:1px solid var(--field-line);font-size:15px;color:#666;padding:10px 11px;background:var(--white)}
.submit{left:644px;top:1984px;width:135px;height:40px;background:var(--navy-deep);color:var(--white);font-family:var(--serif);font-size:20px;text-align:center;line-height:40px;letter-spacing:1px}

/* footer */
.footer{left:0;top:2086px;width:1200px;height:353px;background:var(--navy-deep)}
.on-dark{color:var(--white)}
.foot-brand{left:62px;top:2222px;width:240px;text-align:center;font-family:var(--serif);color:var(--white)}
.foot-brand .name{font-size:27px;line-height:34px;letter-spacing:.5px;white-space:nowrap;display:flex;align-items:center;justify-content:center;gap:8px}
.foot-brand .mark{flex:none;width:11px;height:11px;background:var(--white)}
.foot-brand .tag{font-size:8px;line-height:12px;letter-spacing:2px;border-top:1px solid rgba(255,255,255,.6);margin:3px 12px 0;padding-top:3px;white-space:nowrap}
.foot-about{left:79px;top:2288px;width:240px;font-size:15.5px;line-height:26px}
.foot-head{top:2120px;font-family:var(--serif);font-size:23px;font-weight:400;letter-spacing:1px}
.foot-links{left:351px;top:2162px;list-style:none;font-size:17px;line-height:33px}
.foot-links li::before{content:"›";display:inline-block;width:16px;font-size:22px}
.foot-sub{left:621px;top:2164px;font-size:15px}
.foot-input{left:618px;width:234px;height:36px;background:var(--navy);border:1px solid #3c76a3;font-size:15px;padding:7px 10px}
.foot-btn{left:618px;top:2304px;width:159px;height:46px;background:var(--white);color:var(--navy);font-family:var(--serif);font-size:20px;text-align:center;line-height:46px;letter-spacing:1px}
.foot-contact{left:891px;font-size:15px;line-height:24px;display:flex;gap:12px;align-items:flex-start}
.foot-contact.strong{font-weight:700}
.social{width:52px;height:52px;border-radius:50%;border:2px solid var(--white);display:flex;align-items:center;justify-content:center}
.social.solid{background:var(--white)}
.social .dot{width:10px;height:10px;border-radius:50%;background:var(--white)}
.social.solid .dot{background:var(--navy)}
.foot-rule{left:75px;top:2387px;width:1050px;height:1px;background:rgba(255,255,255,.35)}
.copy{left:0;width:1200px;top:2402px;text-align:center;font-size:15px}
</style>
</head>
<body>

<div class="abs topbar">
  <div class="abs mail">
    <svg width="16" height="12" viewBox="0 0 16 12" fill="none" stroke="#fff" stroke-width="1.5"><rect x="1" y="1" width="14" height="10"/><path d="M1 1l7 6 7-6"/></svg>
    info@briskharbor.com
  </div>
  <div class="abs phone">
    <svg width="20" height="20" viewBox="0 0 24 24" fill="#fff"><path d="M6.6 10.8a15 15 0 0 0 6.6 6.6l2.2-2.2a1 1 0 0 1 1-.25 11.4 11.4 0 0 0 3.6.57 1 1 0 0 1 1 1V20a1 1 0 0 1-1 1A17 17 0 0 1 3 4a1 1 0 0 1 1-1h3.5a1 1 0 0 1 1 1c0 1.25.2 2.45.57 3.57a1 1 0 0 1-.25 1z"/></svg>
    123 456 7890
  </div>
</div>

<div class="abs brand">
  <div class="name"><span class="mark"></span>BRISK HARBOR</div>
  <div class="tag">CLAIMS RECOVERY SERVICES</div>
</div>
<nav>
  <span class="abs nav active" style="left:488px">HOME</span>
  <span class="abs nav" style="left:584px">ABOUT</span>
  <span class="abs nav" style="left:689px">SERVICES</span>
  <span class="abs nav" style="left:815px">CLIENTS</span>
  <span class="abs nav" style="left:932px">BLOG</span>
  <span class="abs nav" style="left:1026px">CONTACT</span>
</nav>

<section class="abs hero" role="img" aria-label="Photo of business people in a meeting around a table with charts">
  <h1>MANAGING YOUR MONEY,<br>RECOVERING YOUR RELATIONSHIPS</h1>
</section>

<div class="abs welcome-mark"></div>
<h2 class="abs section-title welcome-title">WELCOME TO <b>BRISK HARBOR</b></h2>
<p class="abs welcome-text">We are a Claims Recovery and Debt Management Services company based in Dubai, United Arab Emirates. The Brisk Harbor team handles a comprehensive range of debt recoveries, such as invoices; insurance payments; supplier and rent payments; and personal and business loans, for individuals and businesses across an array of industries.</p>

<div class="abs sector" style="left:75px;top:1052px">
  <div class="ring"><svg width="54" height="50" viewBox="0 0 54 50" fill="var(--navy)"><path d="M27 2L2 14h50z"/><rect x="4" y="16" width="46" height="4"/><rect x="8" y="22" width="6" height="18"/><rect x="19" y="22" width="6" height="18"/><rect x="30" y="22" width="6" height="18"/><rect x="41" y="22" width="6" height="18"/><rect x="4" y="42" width="46" height="5"/></svg></div>
  <div class="label">GOVERNMENT<br>ENTITIES</div>
</div>
<div class="abs sector" style="left:345px;top:1052px">
  <div class="ring"><svg width="52" height="46" viewBox="0 0 52 46"><path d="M26 44L5 23A12 12 0 0 1 26 8a12 12 0 0 1 21 15z" fill="var(--navy)"/><path d="M6 24h12l4-8 6 14 4-6h14" fill="none" stroke="#ececec" stroke-width="3"/></svg></div>
  <div class="label">MEDICAL &amp; HEALTH<br>CARE</div>
</div>
<div class="abs sector" style="left:617px;top:1052px">
  <div class="ring"><svg width="34" height="56" viewBox="0 0 34 56" fill="none" stroke="var(--navy)" stroke-width="6" stroke-linecap="round"><path d="M17 3v50"/><path d="M29 14c-3-4-8-5-12-5-6 0-11 3-11 9 0 12 23 7 23 20 0 6-5 9-12 9-5 0-9-2-12-6"/></svg></div>
  <div class="label">BANKS &amp; FINANCE<br>COMPANIES</div>
</div>
<div class="abs sector" style="left:885px;top:1052px">
  <div class="ring"><svg width="62" height="40" viewBox="0 0 62 40" fill="var(--navy)"><path d="M0 6l10-4 4 20-9 3z"/><path d="M62 6l-10-4-4 20 9 3z"/><path d="M13 6l9-2 10 4-8 6c2 2 5 2 7 0l6-5 11 12-14 13c-2 1-4 1-5-1l-13-10-3-17z"/></svg></div>
  <div class="label">SME'S &amp; COMMERCIAL<br>BUSINESS</div>
</div>

<section class="abs services" role="img" aria-label="Faint background of financial charts and world map"></section>
<h2 class="abs section-title services-title">SERVICES <b>WE PROVIDE</b></h2>

<div class="abs service-img" style="left:81px;top:1431px;background:linear-gradient(135deg,#cfdbe6,#8aa3ba 60%,#5d7590)" role="img" aria-label="Photo of a business team meeting"></div>
<h3 class="abs service-title" style="left:311px;top:1428px">Recovery Solutions</h3>
<p class="abs service-text" style="left:311px;top:1464px">Our experience has taught us that when it comes to recovery, it always pays to find the most amicable...</p>
<div class="abs read-more" style="left:311px;top:1547px">READ MORE <svg width="14" height="12" viewBox="0 0 14 12" fill="none" stroke="var(--navy)" stroke-width="2"><path d="M1 1l5 5-5 5M7 1l5 5-5 5"/></svg></div>

<div class="abs service-img" style="left:628px;top:1431px;background:linear-gradient(90deg,#8f8a7e,#c9c2b0 55%,#6f6a5f)" role="img" aria-label="Photo of coin stacks beside a light bulb"></div>
<h3 class="abs service-title" style="left:857px;top:1428px">Debt Management</h3>
<p class="abs service-text" style="left:857px;top:1464px">At Brisk Harbor, we pull together our wisdom and expertise to make debt work for you...</p>
<div class="abs read-more" style="left:857px;top:1547px">READ MORE <svg width="14" height="12" viewBox="0 0 14 12" fill="none" stroke="var(--navy)" stroke-width="2"><path d="M1 1l5 5-5 5M7 1l5 5-5 5"/></svg></div>

<h2 class="abs section-title news-title">LATEST <b>NEWS</b></h2>

<div class="abs news-date" style="top:1738px"><div class="day">11</div><div class="mon">Jun</div></div>
<div class="abs news-item" style="top:1741px"><h3>Lorem Ipsum is dummy text.</h3><p>Lorem Ipsum is dummy text of the printing and type setting industry. <span>READ MORE</span></p></div>
<div class="abs news-date" style="top:1842px"><div class="day">11</div><div class="mon">Jun</div></div>
<div class="abs news-item" style="top:1845px"><h3>Lorem Ipsum is dummy text.</h3><p>Lorem Ipsum is dummy text of the printing and type setting industry. <span>READ MORE</span></p></div>
<div class="abs news-date" style="top:1946px"><div class="day">11</div><div class="mon">Jun</div></div>
<div class="abs news-item" style="top:1949px"><h3>Lorem Ipsum is dummy text.</h3><p>Lorem Ipsum is dummy text of the printing and type setting industry. <span>READ MORE</span></p></div>

<h2 class="abs section-title touch-title">GET IN <b>TOUCH</b></h2>
<div class="abs field" style="left:644px;top:1745px;width:229px;height:40px">Enter Name</div>
<div class="abs field" style="left:893px;top:1745px;width:229px;height:40px">Enter Contact No.</div>
<div class="abs field" style="left:644px;top:1806px;width:478px;height:41px">Enter Email Id</div>
<div class="abs field" style="left:644px;top:1870px;width:478px;height:93px">Enter Message</div>
<div class="abs submit">SUBMIT</div>

<footer class="abs footer"></footer>
<div class="abs foot-brand">
  <div class="name"><span class="mark"></span>BRISK HARBOR</div>
  <div class="tag">CLAIMS RECOVERY SERVICES</div>
</div>
<p class="abs foot-about on-dark">We are a Claims Recovery and Debt Management Services company based in Dubai.</p>

<h4 class="abs foot-head on-dark" style="left:351px">USEFUL LINKS</h4>
<ul class="abs foot-links on-dark">
  <li>Home</li><li>About</li><li>Services</li><li>Clients</li><li>Blog</li><li>Contact</li>
</ul>

<h4 class="abs foot-head on-dark" style="left:621px">NEWSLETTER</h4>
<p class="abs foot-sub on-dark">Subscribe to stay on Brisk Harbor</p>
<div class="abs foot-input on-dark" style="top:2200px">Enter Name</div>
<div class="abs foot-input on-dark" style="top:2252px">Enter Email</div>
<div class="abs foot-btn">SUBSCRIBE</div>

<h4 class="abs foot-head on-dark" style="left:891px">GET IN TOUCH</h4>
<div class="abs foot-contact on-dark" style="top:2164px">
  <svg width="14" height="20" viewBox="0 0 14 20" fill="#fff" style="margin-top:3px"><path d="M7 0a7 7 0 0 0-7 7c0 5 7 13 7 13s7-8 7-13a7 7 0 0 0-7-7zm0 10a3 3 0 1 1 0-6 3 3 0 0 1 0 6z"/></svg>
  <span>Lorem Ipsum is dummy<br>text of the printing.</span>
</div>
<div class="abs foot-contact strong on-dark" style="top:2224px">
  <svg width="16" height="16" viewBox="0 0 24 24" fill="#fff" style="margin-top:4px"><path d="M6.6 10.8a15 15 0 0 0 6.6 6.6l2.2-2.2a1 1 0 0 1 1-.25 11.4 11.4 0 0 0 3.6.57 1 1 0 0 1 1 1V20a1 1 0 0 1-1 1A17 17 0 0 1 3 4a1 1 0 0 1 1-1h3.5a1 1 0 0 1 1 1c0 1.25.2 2.45.57 3.57a1 1 0 0 1-.25 1z"/></svg>
  <span>123 456 7890</span>
</div>
<div class="abs foot-contact on-dark" style="top:2263px">
  <svg width="16" height="12" viewBox="0 0 16 12" fill="none" stroke="#fff" stroke-width="1.5" style="margin-top:6px"><rect x="1" y="1" width="14" height="10"/><path d="M1 1l7 6 7-6"/></svg>
  <span>info@briskharbor.com</span>
</div>
<div class="abs social solid" style="left:888px;top:2301px" role="img" aria-label="Social profile link"><span class="dot"></span></div>
<div class="abs social" style="left:959px;top:2301px" role="img" aria-label="Social profile link"><span class="dot"></span></div>
<div class="abs social" style="left:1032px;top:2301px" role="img" aria-label="Social profile link"><span class="dot"></span></div>

<div class="abs foot-rule"></div>
<p class="abs copy on-dark">© <b>BRISK HARBOR</b> - 2016. All Rights Reserved.</p>

</body>
</html>
```